Lanternfield Drinks business cards

We need a business card design for our new logo. The company is modern, progressive, professional, yet approachable. The key products are ready to drink bottles and cans of coffee based beverages.
These cards will be a critical part of the first impression made by our sales organization, business development team, and all external facing personnel.
Card can be a vertical or horizontal orientation.

Target Market(s)

Customers, suppliers, business partners

Industry/Entity Type

Business

Contact Information for Business Card

Business cards should feature Company Name and Logo.

Font styles to use
Serif

Colors

Designer to choose colors to be used in the design.

Requirements
Must have
• Strong readability of Name, phone #, mobile number and email address.
• Job title, website url, Street Address, and other details can be secondary level readability.
Nice to have
• High impact, simplistic quality design.
• Ok to utilize the 'H in the box' separate from the company name

```html
<!DOCTYPE html>
<html lang="en">
<head>
<meta charset="utf-8">
<title>Lanternfield Drinks – Business Cards</title>
<link href="https://fonts.googleapis.com/css2?family=Cinzel:wght@700&family=Open+Sans:wght@400;600&display=swap" rel="stylesheet">
<style>
  :root{
    --orange:#f05a2a;
    --gold:#e8a020;
    --ink:#2b2b2b;
    --paper:#ffffff;
    --backdrop:#ecebe8;
    --rule:#ffffff;
  }
  *{margin:0;padding:0;box-sizing:border-box}
  html,body{width:1200px;height:900px;overflow:hidden;background:var(--backdrop)}
  .canvas{position:relative;width:1200px;height:900px}
  .card{
    position:absolute;left:320px;width:560px;height:320px;
    background:var(--paper);
    box-shadow:0 2px 6px rgba(0,0,0,.12);
    overflow:hidden;
  }
  .card--front{top:110px}
  .card--back{top:470px}

  /* front */
  .brand{
    position:absolute;left:0;right:0;top:50%;transform:translateY(-50%);
    display:flex;flex-direction:column;align-items:center;gap:14px;
  }
  .brand__square{width:62px;height:62px;border:4px solid var(--orange)}
  .brand__name{
    font-family:"Cinzel",serif;font-weight:700;color:var(--orange);
    font-size:34px;letter-spacing:1px;line-height:1;text-align:center;
  }
  .brand__rule{width:300px;height:2px;background:var(--gold)}

  /* back */
  .band{
    position:absolute;left:0;top:0;bottom:0;width:172px;background:var(--orange);
  }
  .band__mark{
    position:absolute;left:50%;top:50%;
    transform:translate(-50%,-50%) rotate(-90deg);
    display:flex;flex-direction:column;align-items:center;gap:6px;
    white-space:nowrap;
  }
  .band__name{
    font-family:"Cinzel",serif;font-weight:700;color:var(--rule);
    font-size:28px;line-height:1;letter-spacing:1px;
  }
  .band__rule{width:240px;height:2px;background:var(--rule)}

  .contact{
    position:absolute;left:214px;top:70px;
    font-family:"Open Sans",sans-serif;color:var(--ink);
  }
  .contact__name{
    font-family:"Cinzel",serif;font-weight:700;color:var(--orange);
    font-size:19px;letter-spacing:.5px;line-height:1.1;
  }
  .contact__title{font-size:13px;margin-bottom:12px}
  .contact__list{list-style:none}
  .contact__item{display:flex;align-items:center;gap:7px;font-size:14px;line-height:21px}
  .contact__icon{width:15px;height:15px;flex:none}
  .contact__address{margin-top:12px;font-size:14px;line-height:20px}
</style>
</head>
<body>
<div class="canvas">

  <section class="card card--front" aria-label="Card front">
    <div class="brand">
      <div class="brand__square"></div>
      <div class="brand__name">Lanternfield Drinks</div>
      <div class="brand__rule"></div>
    </div>
  </section>

  <section class="card card--back" aria-label="Card back">
    <div class="band">
      <div class="band__mark">
        <div class="band__name">Lanternfield</div>
        <div class="band__rule"></div>
      </div>
    </div>

    <div class="contact">
      <div class="contact__name">Daniel Whitmore</div>
      <div class="contact__title">Managing Director</div>
      <ul class="contact__list">
        <li class="contact__item">
          <svg class="contact__icon" viewBox="0 0 16 16"><rect width="16" height="16" fill="#f05a2a"/><path d="M4 5h8v2H4zM5 8h6v4H5z" fill="#fff"/></svg>
          044-555 012 340
        </li>
        <li class="contact__item">
          <svg class="contact__icon" viewBox="0 0 16 16"><rect width="16" height="16" fill="#f05a2a"/><rect x="5" y="3" width="6" height="10" rx="1" fill="#fff"/><rect x="6" y="4.5" width="4" height="6" fill="#f05a2a"/></svg>
          044-555 012 341
        </li>
        <li class="contact__item">
          <svg class="contact__icon" viewBox="0 0 16 16"><rect width="16" height="16" fill="#f05a2a"/><rect x="3" y="4.5" width="10" height="7" fill="#fff"/><path d="M3 4.5l5 4 5-4" stroke="#f05a2a" fill="none"/></svg>
          info@lanternfield.com
        </li>
        <li class="contact__item">
          <svg class="contact__icon" viewBox="0 0 16 16"><rect width="16" height="16" fill="#f05a2a"/><circle cx="8" cy="8" r="4.5" fill="#fff"/><path d="M3.5 8h9M8 3.5v9" stroke="#f05a2a"/></svg>
          www.lanternfielddrinks.com
        </li>
      </ul>
      <div class="contact__address">12345, Address Goes Here<br>Country Name, 123456.</div>
    </div>
  </section>

</div>
</body>
</html>
```